Business card for event manager / organizer "waiter service"

Draft of a new valuable business card for my company.
Events, personnel service providers, festivals

```html
<!DOCTYPE html>
<html lang="de">
<head>
<meta charset="utf-8">
<title>Jonas Tischservice – Visitenkarte</title>
<link href="https://fonts.googleapis.com/css2?family=Arimo:wght@400;700&display=swap" rel="stylesheet">
<style>
  :root {
    --page: #e8e8e8;
    --card-white: #ffffff;
    --card-dark: #333333;
    --orange: #e8761e;
    --grey-text: #6e6e6e;
    --light-text: #dcdcdc;
    --shirt: #151b24;
  }
  * { box-sizing: border-box; margin: 0; padding: 0; }
  html, body { width: 1200px; height: 802px; overflow: hidden; }
  body {
    background: var(--page);
    font-family: "Arimo", Arial, sans-serif;
    position: relative;
  }
  .card {
    position: absolute;
    top: 226px;
    width: 540px;
    height: 350px;
    box-shadow: 0 6px 18px rgba(0,0,0,.18);
    overflow: hidden;
  }
  .card--front { left: 40px; background: var(--card-white); }
  .card--back { left: 620px; background: var(--card-dark); }

  /* Front */
  .portrait {
    position: absolute;
    right: 0; top: 0;
    width: 210px; height: 350px;
    background: linear-gradient(180deg, #ffffff 0%, #ffffff 16%, #2a2f38 42%, var(--shirt) 100%);
  }
  .brand {
    position: absolute;
    left: 30px; top: 40px;
    display: flex; align-items: center; gap: 10px;
  }
  .brand__square { width: 32px; height: 32px; background: var(--orange); flex: none; }
  .brand__name {
    font-weight: 700; font-size: 22px; color: var(--orange);
    white-space: nowrap;
  }
  .tagline--small {
    position: absolute; left: 72px; top: 76px;
    font-size: 9px; color: var(--grey-text);
    white-space: nowrap;
  }
  .person { position: absolute; left: 30px; top: 120px; }
  .person__name { font-weight: 700; font-size: 22px; color: var(--orange); }
  .person__role { font-size: 14px; color: var(--grey-text); margin-top: 2px; }
  .contacts {
    position: absolute; left: 30px; top: 185px;
    list-style: none;
  }
  .contacts li {
    display: flex; align-items: center; gap: 9px;
    font-size: 14px; color: var(--grey-text);
    height: 23px; white-space: nowrap;
  }
  .contacts svg { width: 13px; height: 13px; flex: none; }
  .contacts .dot { width: 13px; height: 13px; border-radius: 50%; background: var(--orange); flex: none; }

  /* Back */
  .back-logo {
    position: absolute; left: 0; right: 0; top: 135px;
    display: flex; align-items: center; justify-content: center; gap: 14px;
  }
  .back-logo__square { width: 56px; height: 56px; background: var(--orange); flex: none; }
  .back-logo__name { font-weight: 700; font-size: 38px; color: var(--orange); white-space: nowrap; }
  .tagline--large {
    position: absolute; left: 0; right: 0; top: 205px;
    text-align: center; font-size: 14px; color: var(--light-text);
  }
</style>
</head>
<body>

<section class="card card--front">
  <div class="portrait" role="img" aria-label="Porträtfoto des Inhabers im dunklen Hemd"></div>

  <div class="brand">
    <span class="brand__square"></span>
    <span class="brand__name">Jonas Tischservice</span>
  </div>
  <p class="tagline--small">..weil jedes Fest guten Service verdient!</p>

  <div class="person">
    <p class="person__name">Jonas Berkfeld</p>
    <p class="person__role">Inhaber</p>
  </div>

  <ul class="contacts">
    <li>
      <svg viewBox="0 0 16 16"><path fill="var(--orange)" d="M3 1l3 3-2 2c1 2 3 4 5 5l2-2 3 3-2 3C7 15 1 9 1 3z"/></svg>
      02361 555 01 24
    </li>
    <li>
      <svg viewBox="0 0 16 16"><path fill="var(--orange)" d="M3 1l3 3-2 2c1 2 3 4 5 5l2-2 3 3-2 3C7 15 1 9 1 3z"/></svg>
      0170 555 38 17
    </li>
    <li>
      <svg viewBox="0 0 16 16"><rect x="1" y="3" width="14" height="10" fill="var(--orange)"/><path d="M1 3l7 6 7-6" stroke="#fff" stroke-width="1.4" fill="none"/></svg>
      info@jonas-tischservice.de
    </li>
    <li>
      <svg viewBox="0 0 16 16"><circle cx="8" cy="8" r="7" fill="var(--orange)"/><path d="M1 8h14M8 1c3 3 3 11 0 14M8 1c-3 3-3 11 0 14" stroke="#fff" stroke-width="1" fill="none"/></svg>
      www.jonas-tischservice.de
    </li>
    <li>
      <span class="dot"></span>
      jonastischservice
    </li>
    <li>
      <svg viewBox="0 0 16 16"><path fill="var(--orange)" d="M8 1a5 5 0 0 1 5 5c0 4-5 9-5 9S3 10 3 6a5 5 0 0 1 5-5z"/><circle cx="8" cy="6" r="2" fill="#fff"/></svg>
      Lindenweg 14, 45699 Herten
    </li>
  </ul>
</section>

<section class="card card--back">
  <div class="back-logo">
    <span class="back-logo__square"></span>
    <span class="back-logo__name">Jonas Tischservice</span>
  </div>
  <p class="tagline--large">..weil jedes Fest guten Service verdient!</p>
</section>

</body>
</html>
```